Goodlooking website for a company who is working in the IT consultancy

We want a new website designed in WordPress. You can take www.vantoro.nl as an example. It should be a website with some short blocks of information about the company, nice pictures of our partners and our employees. A job page with a clear filter.

Target Market(s)

B2B

Industry/Entity Type

It Company

Coding

Coded - Design and coding required

Number of Pages Required

5+ page

Font styles to use
Sans Serif

Colors
0455a3
34a7d8

Requirements
Must have
• Check briefing

```html
<!DOCTYPE html>
<html lang="en">
<head>
<meta charset="utf-8">
<title>IT &amp; Technology Jobs in Netherlands – Vantoro</title>
<link href="https://fonts.googleapis.com/css2?family=Signika:wght@400;600&family=PT+Sans:wght@400;700&display=swap" rel="stylesheet">
<style>
:root{
  --teal:#3aabc4;
  --teal-dark:#2a8fa8;
  --green:#16ad8f;
  --navy:#1f3b4d;
  --ink:#2f2f2f;
  --muted:#8a8a8a;
  --nav:#7a7a7a;
  --band:#f2f2f2;
  --line:#e4e4e4;
  --btn:#6b6b6b;
  --foot:#333333;
  --foot-bottom:#3a3a3a;
  --foot-text:#b5b5b5;
  --white:#ffffff;
}
*{box-sizing:border-box;margin:0;padding:0}
html,body{width:1098px;height:1200px;overflow:hidden;background:var(--white)}
body{position:relative;font-family:"PT Sans",sans-serif;color:var(--ink)}
.abs{position:absolute}

/* header */
.site-header{position:absolute;left:0;top:0;width:1098px;height:64px;background:var(--white);box-shadow:0 1px 3px rgba(0,0,0,.12);z-index:2}
.brand{position:absolute;left:163px;top:14px;display:flex;align-items:center;gap:10px}
.brand-dot{width:36px;height:36px;border-radius:50%;background:var(--teal)}
.brand-name{font-family:"Signika",sans-serif;font-weight:400;font-size:26px;letter-spacing:2px;color:var(--navy)}
.main-nav{position:absolute;top:0;left:0;height:64px}
.main-nav a{position:absolute;top:0;height:64px;line-height:64px;font-family:"Signika",sans-serif;font-size:8.5px;font-weight:600;letter-spacing:.4px;color:var(--nav);text-decoration:none;text-align:center}
.main-nav a.active{background:var(--teal);color:var(--white)}

/* hero */
.page-hero{position:absolute;left:0;top:64px;width:1098px;height:86px;background:linear-gradient(90deg,#2a9ac0 0%,#3aa6cc 45%,#6bb8d6 75%,#4aa7cc 100%)}
.page-hero h1{position:absolute;left:162px;top:33px;font-family:"Signika",sans-serif;font-weight:600;font-size:17px;color:var(--white)}
.breadcrumb{position:absolute;left:0;top:150px;width:1098px;height:35px;background:var(--band);border-bottom:1px solid var(--line);font-size:9.5px;font-weight:700;color:#444;padding:12px 0 0 162px;letter-spacing:.3px}

/* job cards */
.job-card{position:absolute;left:162px;width:538px;height:98px;background:var(--white);box-shadow:0 0 6px rgba(0,0,0,.1)}
.job-card h2{position:absolute;left:21px;top:18px;font-family:"Signika",sans-serif;font-weight:600;font-size:14px;letter-spacing:.4px;color:var(--ink)}
.job-loc{position:absolute;left:21px;top:48px;display:flex;align-items:center;gap:8px;font-size:9px;color:#555}
.job-meta{position:absolute;left:21px;top:74px;font-size:8.5px;letter-spacing:.7px;color:var(--muted)}
.btn-more{position:absolute;left:428px;top:37px;width:86px;height:23px;border-radius:12px;background:var(--btn);border:2px solid #8f8f8f;color:var(--white);font-family:"Signika",sans-serif;font-weight:600;font-size:7.5px;letter-spacing:.6px;display:flex;align-items:center;justify-content:center;gap:5px}

/* cv form */
.cv-panel{position:absolute;left:715px;top:209px;width:210px;height:355px;background:var(--teal);border-radius:4px}
.cv-panel h3{position:absolute;left:0;width:210px;top:12px;text-align:center;font-family:"Signika",sans-serif;font-weight:600;font-size:13.5px;color:var(--white);letter-spacing:.3px}
.cv-form{position:absolute;left:8px;top:39px;width:194px;height:308px;background:var(--white);border-radius:5px}
.cv-form label{position:absolute;left:13px;font-family:"Signika",sans-serif;font-weight:600;font-size:9.5px;color:#444}
.cv-input{position:absolute;left:13px;width:167px;height:33px;border:1px solid #cfcfcf;font-size:9px;color:#888;padding:11px 0 0 8px}
.file-row{position:absolute;left:13px;top:234px;display:flex;align-items:center;gap:4px;font-size:8.5px;color:#333}
.file-btn{border:1px solid #999;background:#eee;border-radius:2px;padding:1px 6px;font-size:8.5px}
.btn-send{position:absolute;left:13px;top:268px;width:76px;height:27px;border-radius:14px;background:var(--green);color:var(--white);font-family:"Signika",sans-serif;font-weight:600;font-size:9px;letter-spacing:.6px;display:flex;align-items:center;justify-content:center;gap:8px}

/* footer */
.site-footer{position:absolute;left:0;top:821px;width:1098px;height:303px;background:var(--foot)}
.foot-col{position:absolute;top:54px}
.foot-col h4{font-family:"Signika",sans-serif;font-weight:400;font-size:13px;letter-spacing:.8px;color:var(--white);padding-bottom:9px;border-bottom:1px solid #555;position:relative}
.foot-col h4::after{content:"";position:absolute;left:0;bottom:-1px;width:22px;height:2px;background:var(--teal)}
.foot-links{list-style:none;margin-top:14px}
.foot-links li{font-size:10px;letter-spacing:.8px;color:var(--foot-text);height:29px;line-height:21px;border-bottom:1px solid #3f3f3f;margin-bottom:0}
.foot-links li::before{content:"»";margin-right:12px;color:#888}
.contact-item{position:absolute;left:0;display:flex;gap:10px}
.contact-item .lbl{font-size:10.5px;letter-spacing:.6px;color:var(--white)}
.contact-item .val{font-size:10px;letter-spacing:.6px;color:var(--foot-text);line-height:15px;margin-top:4px}
.newsletter-note{font-size:9.5px;color:#9a9a9a;margin-top:26px}
.news-input{width:204px;height:27px;background:var(--white);border:1px solid #ccc;margin-top:14px;font-size:9.5px;color:#999;padding:7px 0 0 9px}
.btn-sub{width:91px;height:27px;border-radius:14px;background:#555;color:var(--white);font-size:10px;display:flex;align-items:center;justify-content:center;gap:7px;margin-top:8px}
.foot-bottom{position:absolute;left:0;top:1124px;width:1098px;height:76px;background:var(--foot-bottom);border-top:1px solid #444}
.social{position:absolute;top:14px;width:29px;height:29px;border-radius:50%;border:1px solid #777}
.copyright{position:absolute;top:55px;left:0;width:1098px;text-align:center;font-size:9.5px;letter-spacing:.8px;color:#999}
</style>
</head>
<body>

<header class="site-header">
  <div class="brand"><span class="brand-dot"></span><span class="brand-name">VANTORO</span></div>
  <nav class="main-nav">
    <a style="left:578px;width:46px">HOME</a>
    <a style="left:640px;width:82px">OUR SOLUTIONS</a>
    <a style="left:741px;width:60px">OUR TEAM</a>
    <a class="active" style="left:810px;width:54px">JOBS</a>
    <a style="left:874px;width:52px">CONTACT</a>
  </nav>
</header>

<section class="page-hero" role="img" aria-label="Glass office tower photograph in blue tones">
  <h1>IT &amp; Technology Jobs in Netherlands</h1>
</section>
<div class="breadcrumb">Home &gt; Jobs</div>

<main>
  <article class="job-card" style="top:209px">
    <h2>Full Stack Developer</h2>
    <div class="job-loc"><svg width="8" height="12" viewBox="0 0 8 12"><path d="M4 0a4 4 0 0 0-4 4c0 3 4 8 4 8s4-5 4-8a4 4 0 0 0-4-4z" fill="#16ad8f"/><circle cx="4" cy="4" r="1.5" fill="#fff"/></svg>Eindhoven</div>
    <div class="job-meta">Published: 18-04-2018 | Reference:#TO108128</div>
    <div class="btn-more">LEARN MORE <svg width="8" height="8" viewBox="0 0 8 8"><circle cx="4" cy="4" r="3.2" fill="none" stroke="#fff" stroke-width="1"/><path d="M3.3 2.4 5 4 3.3 5.6" fill="none" stroke="#fff" stroke-width="1"/></svg></div>
  </article>
  <article class="job-card" style="top:326px">
    <h2>Digital Commercial Excellence Portfolio Manager</h2>
    <div class="job-loc"><svg width="8" height="12" viewBox="0 0 8 12"><path d="M4 0a4 4 0 0 0-4 4c0 3 4 8 4 8s4-5 4-8a4 4 0 0 0-4-4z" fill="#16ad8f"/><circle cx="4" cy="4" r="1.5" fill="#fff"/></svg>Eindhoven</div>
    <div class="job-meta">Published: 18-04-2018 | Reference:#CAPR01278</div>
    <div class="btn-more">LEARN MORE <svg width="8" height="8" viewBox="0 0 8 8"><circle cx="4" cy="4" r="3.2" fill="none" stroke="#fff" stroke-width="1"/><path d="M3.3 2.4 5 4 3.3 5.6" fill="none" stroke="#fff" stroke-width="1"/></svg></div>
  </article>
  <article class="job-card" style="top:444px">
    <h2>Desktop Support Engineer</h2>
    <div class="job-loc"><svg width="8" height="12" viewBox="0 0 8 12"><path d="M4 0a4 4 0 0 0-4 4c0 3 4 8 4 8s4-5 4-8a4 4 0 0 0-4-4z" fill="#16ad8f"/><circle cx="4" cy="4" r="1.5" fill="#fff"/></svg>Houten</div>
    <div class="job-meta">Published: 18-04-2018 | Reference:#TO108128</div>
    <div class="btn-more">LEARN MORE <svg width="8" height="8" viewBox="0 0 8 8"><circle cx="4" cy="4" r="3.2" fill="none" stroke="#fff" stroke-width="1"/><path d="M3.3 2.4 5 4 3.3 5.6" fill="none" stroke="#fff" stroke-width="1"/></svg></div>
  </article>
  <article class="job-card" style="top:562px">
    <h2>Cyber Security Specialist</h2>
    <div class="job-loc"><svg width="8" height="12" viewBox="0 0 8 12"><path d="M4 0a4 4 0 0 0-4 4c0 3 4 8 4 8s4-5 4-8a4 4 0 0 0-4-4z" fill="#16ad8f"/><circle cx="4" cy="4" r="1.5" fill="#fff"/></svg>Eindhoven</div>
    <div class="job-meta">Published: 18-04-2018 | Reference:#TO108128</div>
    <div class="btn-more">LEARN MORE <svg width="8" height="8" viewBox="0 0 8 8"><circle cx="4" cy="4" r="3.2" fill="none" stroke="#fff" stroke-width="1"/><path d="M3.3 2.4 5 4 3.3 5.6" fill="none" stroke="#fff" stroke-width="1"/></svg></div>
  </article>
  <article class="job-card" style="top:679px">
    <h2>C/C++ Software Engineer</h2>
    <div class="job-loc"><svg width="8" height="12" viewBox="0 0 8 12"><path d="M4 0a4 4 0 0 0-4 4c0 3 4 8 4 8s4-5 4-8a4 4 0 0 0-4-4z" fill="#16ad8f"/><circle cx="4" cy="4" r="1.5" fill="#fff"/></svg>Rotterdam</div>
    <div class="job-meta">Published: 18-04-2018 | Reference:#TO108128</div>
    <div class="btn-more">LEARN MORE <svg width="8" height="8" viewBox="0 0 8 8"><circle cx="4" cy="4" r="3.2" fill="none" stroke="#fff" stroke-width="1"/><path d="M3.3 2.4 5 4 3.3 5.6" fill="none" stroke="#fff" stroke-width="1"/></svg></div>
  </article>

  <aside class="cv-panel">
    <h3>Upload Your CV</h3>
    <div class="cv-form">
      <label style="top:20px">Name</label>
      <div class="cv-input" style="top:41px">Your Full Name</div>
      <label style="top:85px">Email</label>
      <div class="cv-input" style="top:106px">Valid Email Address</div>
      <label style="top:150px">Phone</label>
      <div class="cv-input" style="top:171px">Your Contact Number</div>
      <label style="top:215px">Upload CV</label>
      <div class="file-row"><span class="file-btn">Browse...</span>No file selected.</div>
      <div class="btn-send">SEND <svg width="10" height="10" viewBox="0 0 10 10"><path d="M10 0 0 4.5l3 1.2L8 1.5 4 6.3V10l1.8-2.6L8.5 9z" fill="#fff"/></svg></div>
    </div>
  </aside>
</main>

<footer class="site-footer">
  <div class="foot-col" style="left:182px;width:162px">
    <h4>Contact Info</h4>
    <div class="contact-item" style="top:54px">
      <svg width="10" height="13" viewBox="0 0 8 12"><path d="M4 0a4 4 0 0 0-4 4c0 3 4 8 4 8s4-5 4-8a4 4 0 0 0-4-4z" fill="#34a7d8"/><circle cx="4" cy="4" r="1.5" fill="#333"/></svg>
      <div><div class="lbl">Address:</div><div class="val">Lindelaan 14,<br>3512 AB Utrecht</div></div>
    </div>
    <div class="contact-item" style="top:120px">
      <svg width="10" height="12" viewBox="0 0 10 12"><path d="M2 0 4 3 2.8 4.5c.6 1.6 1.7 2.9 3.2 3.7L7.3 7 10 9l-1.5 2.5C4.5 11 1 6.5.5 1.5z" fill="#34a7d8"/></svg>
      <div><div class="lbl">Phone:</div><div class="val" style="font-size:13px;letter-spacing:1.2px;margin-top:6px">030-5550142</div></div>
    </div>
    <div class="contact-item" style="top:176px">
      <svg width="13" height="10" viewBox="0 0 13 10"><rect width="13" height="10" rx="1" fill="#34a7d8"/><path d="M0 1l6.5 5L13 1" fill="none" stroke="#333" stroke-width="1.2"/></svg>
      <div><div class="lbl">Email:</div><div class="val" style="font-size:13px;color:#34a7d8;margin-top:6px">info@vantoro.nl</div></div>
    </div>
  </div>
  <div class="foot-col" style="left:385px;width:118px">
    <h4>Quick Links</h4>
    <ul class="foot-links"><li>Home</li><li>Our Solutions</li><li>Our Team</li><li>Jobs</li><li style="border:none">Contact</li></ul>
  </div>
  <div class="foot-col" style="left:544px;width:126px">
    <h4>Support</h4>
    <ul class="foot-links"><li>Terms of Use</li><li>Privacy Policy</li><li style="border:none">Cookie Policy</li></ul>
  </div>
  <div class="foot-col" style="left:710px;width:205px">
    <h4>Join Our Newsletter</h4>
    <p class="newsletter-note">Subscribe for Job Alerts and Updates!</p>
    <div class="news-input">Enter Your Email</div>
    <div class="btn-sub"><svg width="10" height="10" viewBox="0 0 10 10"><path d="M10 0 0 4.5l3 1.2L8 1.5 4 6.3V10l1.8-2.6L8.5 9z" fill="#fff"/></svg>Subscribe</div>
  </div>
</footer>

<div class="foot-bottom">
  <span class="social" style="left:518px"></span>
  <span class="social" style="left:551px"></span>
  <p class="copyright">Copyright © 2018 VANTORO. All Rights Reserved.</p>
</div>

</body>
</html>
```